Harborlane Products Flyer

Harborlane Lending Group, Inc.
Licensed Mortgage Company
Serving the DMV since 1997
"You open the Harborlane, we'll carry the load"
We specialize in...
FHA Loans
* Credit Scores as low as 500
* 203K Renovation Loans
Conventional Loans
* As little as 1% Down
* Bank Statement for Self-Employed
Investor Loans
* DSCR, & Fix & Flip
* Commercial & New Construction
Other Programs
* HELOCS & Reverse Mortgages
Call today for a free consultation
(800) 914-6027
www.harborlanehomeloans.com
NMLS #731860

```html
<!DOCTYPE html>
<html lang="en">
<head>
<meta charset="utf-8">
<title>Harborlane Products Flyer</title>
<link rel="stylesheet" href="https://fonts.googleapis.com/css2?family=Cinzel:wght@500;600;700&family=Oswald:wght@500;600&family=Montserrat:wght@400;500&display=swap">
<style>
  :root {
    --paper: #ffffff;
    --ink: #0e1a24;
    --navy: #0d1b26;
    --sun: #fdc55c;
    --sun-fold: #f0a93a;
    --sun-soft: #fde6bb;
    --gold: #e4b55e;
    --brand-blue: #23418f;
    --line: #1c2730;
    --stage: #f2f2f2;
  }
  * { box-sizing: border-box; margin: 0; padding: 0; }
  html, body { width: 991px; height: 1200px; overflow: hidden; background: var(--stage); }
  .flyer { position: relative; width: 991px; height: 1200px; background: var(--paper); color: var(--ink); overflow: hidden; }

  .brand { position: absolute; left: 22px; top: 70px; width: 290px; text-align: center; }
  .brand-mark { display: block; width: 22px; height: 22px; border-radius: 50%; background: var(--gold); margin: 0 auto 10px; }
  .brand-name { font-family: "Cinzel", serif; font-weight: 700; font-size: 22px; line-height: 1.15; color: var(--brand-blue); }
  .brand-tagline { font-family: "Montserrat", sans-serif; font-size: 10.5px; color: var(--brand-blue); margin-top: 8px; }
  .brand-est { font-family: "Montserrat", sans-serif; font-weight: 500; font-size: 10px; letter-spacing: 2px; color: var(--ink); margin-top: 4px; }

  .call { position: absolute; left: 515px; top: 58px; }
  .call-icon { position: absolute; left: 0; top: 6px; width: 58px; height: 58px; }
  .call-lead { position: absolute; left: 74px; top: 4px; white-space: nowrap; font-family: "Cinzel", serif; font-weight: 500; font-size: 13px; letter-spacing: .5px; }
  .call-number { position: absolute; left: 72px; top: 18px; white-space: nowrap; font-family: "Cinzel", serif; font-weight: 600; font-size: 40px; letter-spacing: 1px; }
  .since { position: absolute; right: 60px; top: 142px; white-space: nowrap; font-family: "Cinzel", serif; font-weight: 600; font-size: 23px; letter-spacing: 1px; }

  .photo { position: absolute; left: 0; top: 212px; width: 991px; height: 367px;
    background: linear-gradient(115deg, #ebe6e1 0%, #c59a7a 30%, #8a5a3e 48%, #d8cbc0 70%, #efeeec 100%); }

  .hero-panel { position: absolute; left: 510px; top: 190px; width: 448px; height: 416px; background: var(--sun); padding: 14px 28px 0 0; text-align: right; font-family: "Oswald", sans-serif; font-weight: 500; }
  .fold { position: absolute; top: 190px; width: 0; height: 0; border-bottom: 21px solid var(--sun-fold); }
  .fold-left { left: 494px; border-left: 16px solid transparent; }
  .fold-right { left: 958px; border-right: 16px solid transparent; }
  .hero-label { font-size: 26px; line-height: 38px; }
  .hero-line { font-size: 58px; line-height: 64px; margin-top: 36px; }
  .hero-name { font-weight: 600; font-size: 64px; line-height: 90px; }
  .hero-close { font-size: 44px; line-height: 54px; }
  .hero-nmls { font-size: 27px; line-height: 30px; margin-top: 46px; }

  .specialize { position: absolute; left: 45px; top: 632px; font-family: "Cinzel", serif; font-weight: 600; font-size: 42px; letter-spacing: 1.5px; }

  .programs { position: absolute; left: 43px; top: 718px; display: grid; grid-template-columns: 445px 445px; column-gap: 15px; row-gap: 33px; }
  .program { height: 118px; border: 1.5px solid var(--line); display: flex; align-items: center; padding-left: 14px; }
  .program-icon { flex: none; width: 70px; height: 70px; border-radius: 50%; background: var(--sun-soft); display: flex; align-items: center; justify-content: center; margin-right: 26px; }
  .program-icon svg { width: 42px; height: 42px; }
  .program-title { font-family: "Cinzel", serif; font-weight: 600; font-size: 19px; letter-spacing: .8px; margin-bottom: 8px; }
  .program-list { list-style: none; font-family: "Montserrat", sans-serif; font-size: 14.5px; line-height: 25px; }

  .about { position: absolute; left: 45px; top: 1022px; width: 460px; font-family: "Montserrat", sans-serif; font-size: 14px; line-height: 28px; }
  .badges { position: absolute; left: 653px; top: 1043px; display: flex; align-items: center; gap: 22px; }
  .badge { background: #d6dbe3; }
  .badge-square { width: 40px; height: 40px; background: #2b4a9a; }
  .badge-home { width: 46px; height: 36px; background: #3a3a3a; }
  .badge-wide { width: 118px; height: 30px; background: #b23a3a; }

  .footer { position: absolute; left: 0; top: 1138px; width: 991px; height: 62px; background: var(--navy); display: flex; align-items: center; justify-content: center; font-family: "Cinzel", serif; color: var(--gold); }
  .footer small { font-size: 14px; letter-spacing: 1px; }
  .footer strong { font-weight: 500; font-size: 20px; letter-spacing: 2.5px; }
</style>
</head>
<body>
<main class="flyer">

  <header class="brand">
    <span class="brand-mark"></span>
    <div class="brand-name">Harborlane Lending Group, Inc.</div>
    <div class="brand-tagline">You open the Harborlane, we'll carry the load</div>
    <div class="brand-est">EST. 1997</div>
  </header>

  <div class="call">
    <svg class="call-icon" viewBox="0 0 60 60" fill="none" stroke="#0e1a24" stroke-width="3" stroke-linecap="round" stroke-linejoin="round">
      <path d="M14 8 l9 11 -5 6 c3 7 8 12 15 15 l6 -5 11 9 -6 8 c-18 -1 -37 -20 -38 -38 z"/>
      <path d="M34 12 a14 14 0 0 1 14 14"/>
      <path d="M36 3 a22 22 0 0 1 21 21"/>
    </svg>
    <div class="call-lead">Call today for a free consultation</div>
    <div class="call-number">(800) 914-6027</div>
  </div>
  <div class="since">Serving the DMV since 1997</div>

  <div class="photo" role="img" aria-label="Photo of a smiling family of four sitting together on a white bed"></div>

  <span class="fold fold-left"></span>
  <span class="fold fold-right"></span>
  <section class="hero-panel">
    <div class="hero-label">Licensed Mortgage Company</div>
    <div class="hero-line">You Open The</div>
    <div class="hero-name">Harborlane</div>
    <div class="hero-close">We’ll Carry The Load</div>
    <div class="hero-nmls">NMLS #731860</div>
  </section>

  <h2 class="specialize">We specialize in...</h2>

  <section class="programs">
    <article class="program">
      <div class="program-icon">
        <svg viewBox="0 0 42 42" fill="none" stroke="#0e1a24" stroke-width="1.8" stroke-linecap="round" stroke-linejoin="round">
          <circle cx="26" cy="11" r="7"/><path d="M26 7v8M24 9h3a1.5 1.5 0 0 1 0 3h-2a1.5 1.5 0 0 0 0 3h3"/>
          <path d="M4 30c6-6 10-6 15-3h7a2 2 0 0 1 0 4h-7M20 31l12-5a3 3 0 0 1 3 4l-12 7c-6 2-12 0-19 0"/>
        </svg>
      </div>
      <div>
        <h3 class="program-title">FHA Loans</h3>
        <ul class="program-list"><li>* Credit Scores as low as 500</li><li>* 203K Renovation Loans</li></ul>
      </div>
    </article>
    <article class="program">
      <div class="program-icon">
        <svg viewBox="0 0 42 42" fill="none" stroke="#0e1a24" stroke-width="1.8" stroke-linecap="round" stroke-linejoin="round">
          <path d="M6 10h12l8 4h8v8h-8l-6-3M34 10v14"/>
          <circle cx="15" cy="28" r="7"/><path d="M15 24v8M13 26h3a1 1 0 0 1 0 2h-2a1 1 0 0 0 0 2h3"/>
        </svg>
      </div>
      <div>
        <h3 class="program-title">Conventional Loans</h3>
        <ul class="program-list"><li>* As little as 1% Down</li><li>* Bank Statement for Self-Employed</li></ul>
      </div>
    </article>
    <article class="program">
      <div class="program-icon">
        <svg viewBox="0 0 42 42" fill="none" stroke="#0e1a24" stroke-width="1.8" stroke-linecap="round" stroke-linejoin="round">
          <path d="M4 20L21 7l17 13M9 17v18h24V17"/><circle cx="21" cy="19" r="3"/>
          <rect x="6" y="26" width="11" height="9" fill="#0e1a24"/><path d="M26 35v-8h5v8"/>
        </svg>
      </div>
      <div>
        <h3 class="program-title">Investor Loans</h3>
        <ul class="program-list"><li>* DSCR, &amp; Fix &amp; Flip</li><li>* Commercial &amp; New Construction</li></ul>
      </div>
    </article>
    <article class="program">
      <div class="program-icon">
        <svg viewBox="0 0 42 42" fill="none" stroke="#0e1a24" stroke-width="1.8" stroke-linecap="round" stroke-linejoin="round">
          <path d="M5 9h10M5 14h10M27 9h10M27 14h10"/><circle cx="21" cy="11" r="6"/>
          <path d="M4 30c6-5 10-5 15-2h7a2 2 0 0 1 0 4h-7M20 32l12-5a3 3 0 0 1 3 4l-12 6c-6 2-12 0-19 0"/>
        </svg>
      </div>
      <div>
        <h3 class="program-title">Other Programs</h3>
        <ul class="program-list"><li>* HELOCS &amp; Reverse Mortgages</li></ul>
      </div>
    </article>
  </section>

  <p class="about">We have served the MD, DC &amp; VA area by providing an array of mortgage loan products tailored to our clients unique needs and desires.</p>

  <div class="badges">
    <span class="badge badge-square"></span>
    <span class="badge badge-home"></span>
    <span class="badge badge-wide"></span>
  </div>

  <footer class="footer"><small>www.</small><strong>HARBORLANEHOMELOANS</strong><small>.com</small></footer>
</main>
</body>
</html>
```